KOVA! Card

The single side "business card" will be utilized to write down product information for our customers. The card needs to include our logo in josefin font and read KOVA! on the front. Our brand colors are espresso brown and copper. The back needs to be white (blank) to allow us to write information down. We want modern, bold, clean and fun.
I have attached a copy of our logo but you do not have to utilize exactly as shown.

```html
<!DOCTYPE html>
<html lang="en">
<head>
<meta charset="utf-8">
<title>KOVA! Card</title>
<link rel="stylesheet" href="https://fonts.googleapis.com/css2?family=Josefin+Sans:wght@300;400&display=swap">
<style>
  :root {
    --page-bg: #e4e2e6;
    --card-white: #ffffff;
    --espresso: #2a1810;
    --copper: #b87333;
    --photo-dark: #4a3428;
    --photo-mid: #7a5a3c;
    --photo-gold: #c9a24a;
    --band-text: #f4efe9;
  }
  * { margin: 0; padding: 0; box-sizing: border-box; }
  html, body {
    width: 1200px;
    height: 900px;
    overflow: hidden;
  }
  body {
    background: var(--page-bg);
    font-family: "Josefin Sans", sans-serif;
    position: relative;
  }
  .card {
    position: absolute;
    left: 400px;
    top: 50px;
    width: 400px;
    height: 800px;
    background: var(--card-white);
    box-shadow: 0 6px 20px rgba(0, 0, 0, 0.18);
    overflow: hidden;
  }
  .card__product-photo {
    position: absolute;
    left: 56px;
    top: 138px;
    width: 344px;
    height: 116px;
    border-radius: 58px 0 0 58px;
    background: linear-gradient(90deg, var(--photo-dark) 0%, var(--photo-mid) 45%, var(--photo-gold) 62%, var(--photo-mid) 80%, var(--photo-dark) 100%);
    opacity: 0.85;
  }
  .card__brand {
    position: absolute;
    left: 60px;
    right: 40px;
    top: 360px;
    text-align: right;
    color: var(--espresso);
  }
  .card__brand-name {
    font-weight: 300;
    font-size: 66px;
    line-height: 1;
    letter-spacing: 3px;
  }
  .card__brand-tagline {
    margin-top: 10px;
    font-weight: 400;
    font-size: 22px;
    letter-spacing: 0.5px;
  }
  .card__band {
    position: absolute;
    left: 0;
    bottom: 0;
    width: 100%;
    height: 188px;
    background: var(--espresso);
  }
  .card__wordmark {
    position: absolute;
    right: 14px;
    bottom: 10px;
    font-weight: 300;
    font-size: 60px;
    line-height: 1;
    color: var(--band-text);
    letter-spacing: 2px;
  }
</style>
</head>
<body>
  <main class="card">
    <div class="card__product-photo" role="img" aria-label="Photo of a dark bangle bracelet with gold inlay and a diamond-set round clasp"></div>
    <div class="card__brand">
      <p class="card__brand-name">aldermoor</p>
      <p class="card__brand-tagline">Jewelry &amp; Design Studio</p>
    </div>
    <div class="card__band">
      <p class="card__wordmark">kova!</p>
    </div>
  </main>
</body>
</html>
```